Business card for Sports Apparel business

DOUBLE SIDED DESIGN
We need business cards for a new sports apparel business. We are developing a protective headband for soccer initially.
Torvalle is focused on designing and developing head protection products to reduce the likelihood of concussion when playing sports. Exploring and understanding medical insights, material science research, current and former players experiences and governing bodies guidelines has allowed Torvalle to develop the safety, style, form and function requirements of a suitable product to bring to market.
Target Market(s)
Mums buying kits for the sons and daughters. Amateur footballers.
Industry/Entity Type
Sporting Good
Contact Information for Business Card
Martin Ashworth - CEO
Mobile: +44 7431589027
Email: martin@torvalle.co.uk
Tel: 0208 5519372
Helena Pargeter - COO
Mob: +44 7385 640117
Email: helena@torvalle.co.uk
Tel: 0208 5519372
Duncan Farrow - CCO
Mob: +44 7564 293081
Email: duncan@torvalle.co.uk
Tel: 0208 5519372
Look and feel
Each slider illustrates characteristics of the customer's brand and the style your logo design should communicate.

```html
<!DOCTYPE html>
<html lang="en">
<head>
<meta charset="utf-8">
<title>Torvalle business card</title>
<link rel="stylesheet" href="https://fonts.googleapis.com/css2?family=Open+Sans:wght@400;700&family=Ubuntu:wght@400;500&display=swap">
<style>
  :root {
    --page-bg: #2f3d45;
    --band-email: #3f8fc1;
    --band-tel: #7394c4;
    --band-mobile: #356ca1;
    --band-dark-1: #474747;
    --band-dark-2: #333333;
    --band-dark-3: #1c1c1c;
    --ink-light: #f4f4f4;
    --ink-soft: #d9d9d9;
    --accent: #6f8fc6;
    --icon-dot: #3a6fa3;
  }
  * { box-sizing: border-box; margin: 0; padding: 0; }
  html, body { width: 1200px; height: 900px; overflow: hidden; }
  body {
    background: var(--page-bg);
    display: flex;
    flex-direction: column;
    align-items: center;
    justify-content: center;
    gap: 40px;
    font-family: "Open Sans", sans-serif;
  }
  .card {
    width: 620px;
    height: 370px;
    display: flex;
    overflow: hidden;
    border-radius: 3px;
    box-shadow: 0 10px 24px rgba(0,0,0,.35);
  }
  .band { flex: 1; position: relative; overflow: hidden; }

  /* Contact side */
  .band--email { background: var(--band-email); }
  .band--tel { background: var(--band-tel); }
  .band--mobile { background: var(--band-mobile); }
  .contact {
    position: absolute;
    top: 40px;
    right: 8px;
    text-align: right;
    color: var(--ink-light);
  }
  .contact__label { font-weight: 700; font-size: 17px; letter-spacing: .3px; }
  .contact__value { font-size: 15px; margin-top: 2px; white-space: nowrap; }
  .contact__icon {
    position: absolute;
    right: -30px;
    top: 205px;
    width: 120px;
    height: 110px;
  }
  .band--mobile .contact__icon { right: -12px; width: 80px; height: 120px; top: 195px; }

  /* Identity side */
  .band--dark-1 { background: var(--band-dark-1); }
  .band--dark-2 { background: var(--band-dark-2); }
  .band--dark-3 { background: var(--band-dark-3); }
  .identity {
    position: absolute;
    inset: 0;
    display: flex;
    flex-direction: column;
    align-items: center;
    color: var(--ink-light);
    font-family: "Ubuntu", sans-serif;
  }
  .identity__brand {
    margin-top: 95px;
    display: flex;
    align-items: center;
    gap: 14px;
    font-weight: 500;
    font-size: 62px;
    letter-spacing: 2px;
    color: var(--ink-light);
  }
  .identity__mark { width: 22px; height: 22px; background: var(--accent); }
  .identity__name { margin-top: 58px; font-size: 32px; font-weight: 500; letter-spacing: .5px; }
  .identity__role { font-size: 20px; letter-spacing: 3px; color: var(--ink-soft); margin-top: 2px; }
  .card--identity { position: relative; }
</style>
</head>
<body>
  <section class="card card--contact" aria-label="Contact side">
    <div class="band band--email">
      <div class="contact">
        <div class="contact__label">EMAIL</div>
        <div class="contact__value">martin@torvalle.co.uk</div>
      </div>
      <svg class="contact__icon" viewBox="0 0 120 110" aria-hidden="true">
        <rect x="4" y="10" width="130" height="90" rx="8" fill="var(--ink-light)"/>
        <path d="M4 18 L68 62 L134 18" fill="none" stroke="var(--band-email)" stroke-width="7"/>
      </svg>
    </div>
    <div class="band band--tel">
      <div class="contact">
        <div class="contact__label">TEL</div>
        <div class="contact__value">0208 5519372</div>
      </div>
      <svg class="contact__icon" viewBox="0 0 120 110" aria-hidden="true">
        <path d="M10 40 Q10 14 70 14 Q130 14 130 40 L130 50 L105 50 L105 38 L35 38 L35 50 L10 50 Z" fill="var(--ink-light)"/>
        <path d="M30 54 L110 54 L125 100 L16 100 Z" fill="var(--ink-light)"/>
        <g fill="var(--icon-dot)">
          <circle cx="58" cy="66" r="4"/><circle cx="72" cy="66" r="4"/><circle cx="86" cy="66" r="4"/>
          <circle cx="58" cy="78" r="4"/><circle cx="72" cy="78" r="4"/><circle cx="86" cy="78" r="4"/>
          <circle cx="58" cy="90" r="4"/><circle cx="72" cy="90" r="4"/><circle cx="86" cy="90" r="4"/>
        </g>
      </svg>
    </div>
    <div class="band band--mobile">
      <div class="contact">
        <div class="contact__label">MOBILE</div>
        <div class="contact__value">+44 7431589027</div>
      </div>
      <svg class="contact__icon" viewBox="0 0 80 120" aria-hidden="true">
        <rect x="4" y="4" width="72" height="112" rx="10" fill="var(--ink-light)"/>
        <rect x="11" y="16" width="58" height="78" rx="2" fill="var(--band-mobile)"/>
        <rect x="46" y="101" width="16" height="7" rx="3" fill="var(--band-mobile)"/>
      </svg>
    </div>
  </section>

  <section class="card card--identity" aria-label="Name side">
    <div class="band band--dark-1"></div>
    <div class="band band--dark-2"></div>
    <div class="band band--dark-3"></div>
    <div class="identity">
      <div class="identity__brand"><span class="identity__mark"></span>TORVALLE</div>
      <div class="identity__name">Martin Ashworth - CEO</div>
      <div class="identity__role">chief executive officer</div>
    </div>
  </section>
</body>
</html>
```